Birch Hauling Business Card Design Project

We need a new company business card. We provide professional timber harvesting (logging) and forest management services. I'm open to any creative design. Most company caps and shirts are navy blue and Light grey. Logo does not necessarily have to contain those colors. Logo containing picture of logging equipment, log truck, trees, or logs are acceptable. Be creative. Final logo should communicate our company's pride and professionalism in the East Texas Timber Industry.
Updates

Target Market(s)

Timber owners, sawmills, and forestry professionals

Industry/Entity Type

Business

Requirements
Must have
• Must have Contact Info.
Phone: 936-402-5917
address: PO Box 4830
Pine Hollow, Tx 75990
www.jmbirchhauling.example
jmbirchhauling@mailbox.example
Owner: Jared Marsh

Or design must leave room for this info.

```html
<!DOCTYPE html>
<html lang="en">
<head>
<meta charset="utf-8">
<title>Birch Hauling Business Card</title>
<link rel="stylesheet" href="https://fonts.googleapis.com/css2?family=Lato:wght@400;700;900&display=swap">
<style>
  :root {
    --navy: #3f3f94;
    --grey-text: #7a7a7a;
    --grey-band: #87888b;
    --card: #ffffff;
    --backdrop: #e9e9e9;
    --divider: #333333;
  }
  * { box-sizing: border-box; margin: 0; padding: 0; }
  html, body {
    width: 1200px; height: 960px; overflow: hidden;
    background: var(--backdrop);
    font-family: "Lato", Arial, sans-serif;
  }
  .card {
    position: absolute; left: 270px; width: 645px; height: 368px;
    background: var(--card);
    box-shadow: 0 3px 8px rgba(0,0,0,0.25);
    overflow: hidden;
  }
  .card--front { top: 83px; display: flex; align-items: center; justify-content: center; }
  .card--back { top: 507px; }

  .brand { display: flex; align-items: center; }
  .brand__name { color: var(--navy); font-weight: 900; letter-spacing: -0.5px; line-height: 1; white-space: nowrap; }
  .brand__rule { background: var(--divider); width: 2px; }
  .brand__text { color: var(--grey-text); line-height: 1.25; white-space: nowrap; }
  .brand__title { font-weight: 700; }
  .brand__slogan { font-weight: 400; }

  .card--front .brand__name { font-size: 38px; }
  .card--front .brand__rule { height: 54px; margin: 0 18px; }
  .card--front .brand__text { font-size: 22px; }

  .card--back .brand { position: absolute; left: 46px; top: 59px; }
  .card--back .brand__name { font-size: 22px; }
  .card--back .brand__rule { height: 36px; margin: 0 12px; width: 1.5px; }
  .card--back .brand__text { font-size: 14.5px; }

  .person { position: absolute; left: 46px; top: 153px; }
  .person__name { color: var(--navy); font-weight: 700; font-size: 20px; text-transform: uppercase; line-height: 1.1; }
  .person__role { color: var(--grey-text); font-size: 15px; line-height: 1.1; }

  .address { position: absolute; left: 46px; top: 232px; color: var(--grey-text); font-size: 15px; line-height: 19px; font-style: normal; }

  .contacts { position: absolute; left: 45px; top: 284px; list-style: none; color: var(--grey-text); font-size: 15px; }
  .contacts li { display: flex; align-items: center; height: 18.5px; }
  .contacts svg { width: 15px; height: 13px; margin-right: 13px; fill: var(--navy); }

  .wave { position: absolute; left: 0; top: 0; width: 645px; height: 368px; }
</style>
</head>
<body>
  <section class="card card--front">
    <div class="brand">
      <span class="brand__name">Birch Hauling</span>
      <span class="brand__rule"></span>
      <div class="brand__text">
        <div class="brand__title">Company Name</div>
        <div class="brand__slogan">Your Slogan</div>
      </div>
    </div>
  </section>

  <section class="card card--back">
    <svg class="wave" viewBox="0 0 645 368" aria-hidden="true">
      <path d="M468,0 C432,60 430,125 468,200 C508,275 522,320 522,368 L645,368 L645,0 Z" fill="var(--grey-band)"/>
      <path d="M475,0 C442,58 440,120 482,195 C528,272 550,320 550,368 L645,368 L645,0 Z" fill="var(--navy)" stroke="#ffffff" stroke-width="2.5"/>
    </svg>

    <div class="brand">
      <span class="brand__name">Birch Hauling</span>
      <span class="brand__rule"></span>
      <div class="brand__text">
        <div class="brand__title">Company Name</div>
        <div class="brand__slogan">Your Slogan</div>
      </div>
    </div>

    <div class="person">
      <div class="person__name">Jared Marsh</div>
      <div class="person__role">Owner</div>
    </div>

    <address class="address">PO Box 4830<br>Pine Hollow, Tx 75990</address>

    <ul class="contacts">
      <li>
        <svg viewBox="0 0 16 13"><path d="M1 4 C1 1 15 1 15 4 L15 5 L11.5 5 L11.5 3.6 C10 3 6 3 4.5 3.6 L4.5 5 L1 5 Z"/><path d="M4 6 L12 6 L14 12 L2 12 Z"/></svg>
        <span>936-402-5917</span>
      </li>
      <li>
        <svg viewBox="0 0 16 13"><path d="M1 1 H15 V12 H1 Z M2.5 2.5 L8 7 L13.5 2.5 Z M2.5 4 V10.5 H13.5 V4 L8 8.6 Z" fill-rule="evenodd"/></svg>
        <span>jmbirchhauling@mailbox.example</span>
      </li>
      <li>
        <svg viewBox="0 0 16 13"><path d="M1 1 H15 V10 H1 Z M2.5 2.5 V8.5 H13.5 V2.5 Z M5 11 H11 V12.5 H5 Z" fill-rule="evenodd"/></svg>
        <span>www.jmbirchhauling.example</span>
      </li>
    </ul>
  </section>
</body>
</html>
```